Business Card Design Project

This is the first time we use our new logo. We need a business card that we can use both on our institutional corporate relationships and also that works for our staff that deals with consumers directly.

VELUNDA is a new company dedicated to empower consumers and to provide them with the best choices for specialized health care using the latest telemedicine technology (medicine at a distance via videoconference).

We want to print this cards in high quality materials and process. We will like designs that allow us to use UV spot varnish and other techniques that will differentiate us.

We are including Two different versions of Color logos. In addition we are including white over black background logos. Those can be used replacing the black for a color.

Please note this is the first time we will be creating any corporate materials with our new logo and colors.

Target Market(s)

34+ consumers of medium high and high socioeconomic levels.

Industry/Entity Type

Health

Requirements
Must have
• Our logo on its original colors
Should not have
• Any other graphical element or design that is not our logo

```html
<!DOCTYPE html>
<html lang="en">
<head>
<meta charset="utf-8">
<title>VELUNDA Business Card Set</title>
<link rel="stylesheet" href="https://fonts.googleapis.com/css2?family=Jost:wght@400;500;700&display=swap">
<style>
  :root {
    --stage: #d6bf a4;
    --stage: #d8c2a6;
    --ink: #111111;
    --brand-blue: #1c5884;
    --brand-teal: #22a699;
    --brand-sky: #5bb8e3;
    --paper: #ffffff;
    --steel-light: #eeeeee;
    --steel-mid: #c9c9c9;
    --steel-dark: #3a3a3a;
    --card-radius: 22px;
  }
  * { box-sizing: border-box; margin: 0; padding: 0; }
  html, body { width: 1200px; height: 788px; overflow: hidden; }
  body {
    position: relative;
    background: var(--stage);
    font-family: "Jost", "Futura", sans-serif;
    color: var(--ink);
  }
  .view-label {
    position: absolute;
    width: 525px;
    text-align: center;
    font-size: 21px;
    font-weight: 400;
    color: var(--ink);
  }
  .card {
    position: absolute;
    width: 525px;
    height: 300px;
    border-radius: var(--card-radius);
    overflow: hidden;
  }
  .card--front { left: 54px; top: 74px; background: linear-gradient(180deg, var(--steel-light), var(--steel-mid)); }
  .card--back-white { left: 622px; top: 74px; background: var(--paper); }
  .card--back-steel { left: 54px; top: 445px; background: linear-gradient(180deg, #f2f2f2 0%, #b9b9b9 45%, var(--steel-dark) 100%); }
  .card--back-blue { left: 622px; top: 445px; background: var(--brand-blue); }

  .wordmark {
    position: absolute;
    display: flex;
    align-items: center;
    gap: 14px;
    font-weight: 700;
    color: var(--brand-blue);
    letter-spacing: 2px;
    line-height: 1;
  }
  .wordmark__dot {
    border-radius: 50%;
    background: var(--brand-teal);
    flex: none;
  }
  .card--front .wordmark { left: 36px; top: 66px; font-size: 34px; }
  .card--front .wordmark__dot { width: 40px; height: 40px; }
  .card--back-white .wordmark { left: 100px; top: 118px; font-size: 50px; }
  .card--back-white .wordmark__dot { width: 64px; height: 64px; }
  .card--back-steel .wordmark { left: 100px; top: 128px; font-size: 48px; }
  .card--back-steel .wordmark__dot { width: 62px; height: 62px; }
  .card--back-blue .wordmark {
    left: 0; right: 0; top: 36px;
    flex-direction: column; gap: 34px;
    color: var(--paper); font-size: 50px;
  }
  .card--back-blue .wordmark__dot { width: 90px; height: 90px; }

  .wave { position: absolute; left: 0; top: 0; width: 525px; height: 300px; }

  .holder { position: absolute; left: 32px; top: 145px; }
  .holder__name { font-size: 18px; font-weight: 500; }
  .holder__role { font-size: 13px; margin-top: 2px; }
  .holder__phone { font-size: 14px; margin-top: 16px; }
  .key { font-weight: 700; font-style: italic; }

  .contact {
    position: absolute;
    right: 19px; top: 181px;
    text-align: right;
    color: var(--paper);
    font-size: 13.5px;
    line-height: 21px;
    list-style: none;
  }
  .contact__address { line-height: 18px; margin-top: 1px; }

  .site {
    position: absolute;
    left: 0; right: 0; bottom: 22px;
    text-align: center;
    font-size: 16px;
    letter-spacing: 3px;
  }
  .card--back-white .site { color: #333333; bottom: 22px; }
  .card--back-steel .site, .card--back-blue .site { color: var(--paper); }
</style>
</head>
<body>
  <h2 class="view-label" style="left:54px; top:33px;">Front</h2>
  <h2 class="view-label" style="left:622px; top:33px;">Back - 1</h2>
  <h2 class="view-label" style="left:54px; top:403px;">Back - 2</h2>
  <h2 class="view-label" style="left:622px; top:403px;">Back - 3</h2>

  <section class="card card--front">
    <svg class="wave" viewBox="0 0 525 300" aria-hidden="true">
      <path d="M0,262 C120,292 230,262 305,195 C375,135 450,108 525,102 L525,112 C450,118 380,145 312,202 C235,270 120,298 0,270 Z" fill="var(--brand-teal)"/>
      <path d="M0,240 C60,262 110,272 150,270 C90,282 40,282 0,268 Z" fill="var(--brand-sky)"/>
      <path d="M0,280 C120,305 235,275 312,210 C380,152 452,122 525,116 L525,300 L0,300 Z" fill="var(--brand-blue)"/>
    </svg>
    <div class="wordmark"><span class="wordmark__dot"></span><span>VELUNDA</span></div>
    <div class="holder">
      <p class="holder__name">Your Name</p>
      <p class="holder__role">Designation</p>
      <p class="holder__phone"><span class="key">p</span> : +12 345 67890</p>
    </div>
    <ul class="contact">
      <li><span class="key">f</span> : +12 345 67890</li>
      <li><span class="key">e</span> : info@website.com</li>
      <li><span class="key">w</span> : www.website.com</li>
      <li class="contact__address">#0000, Street Name<br>Area Name, Country Code</li>
    </ul>
  </section>

  <section class="card card--back-white">
    <div class="wordmark"><span class="wordmark__dot"></span><span>VELUNDA</span></div>
    <p class="site">www.website.com</p>
  </section>

  <section class="card card--back-steel">
    <div class="wordmark"><span class="wordmark__dot"></span><span>VELUNDA</span></div>
    <p class="site">www.website.com</p>
  </section>

  <section class="card card--back-blue">
    <div class="wordmark"><span class="wordmark__dot"></span><span>VELUNDA</span></div>
    <p class="site">www.website.com</p>
  </section>
</body>
</html>
```